Biz Card

MARKETING today is the most rapidly changing business discipline. Media options to reach customers, actual customer preferences and consumer buying decisions change by the minute . . . no, by the second. The behavioral data generated by all aspects of the business and the new technologies that put the data to work together produce the potential to generate business intelligence and guide smart resource allocation to influence purchase and retention. However, to realize this potential, marketing professionals at all levels and in all organizations must continuously improve their skills not just from on-the-job training but by learning from masters in the field. The Bright Horizon Guild is the training center that serves this professional development need.model logos:msi.orgama.orgcontentmarketinginstitute.comBook covers on MarketingMetrics, Marketing Anaytics
Industry/Entity Type
Business
Contact Information for Business Card
Roy A. YoungCEOMarketing Science Academyphone: 310-601-4755email: roy@marketingscience.comAddress:437 South Rexford DriveBeverly Hills, CA 89377
Look and feel
Each slider illustrates characteristics of the customer's brand and the style your logo design should communicate.

```html
<!DOCTYPE html>
<html lang="en">
<head>
<meta charset="utf-8">
<title>Bright Horizon Guild – Business Card</title>
<link href="https://fonts.googleapis.com/css2?family=Jost:wght@400;500&display=swap" rel="stylesheet">
<style>
  :root {
    --backdrop: #5c5c5e;
    --card: #eff4da;
    --ink: #3b3839;
    --accent: #a6c63a;
    --cream: #eff4da;
  }
  * { margin: 0; padding: 0; box-sizing: border-box; }
  html, body {
    width: 1200px; height: 900px; overflow: hidden;
    background: var(--backdrop);
    font-family: "Jost", "Futura", sans-serif;
    color: var(--ink);
  }
  .canvas {
    width: 1200px; height: 900px;
    display: flex; align-items: center; justify-content: center;
  }
  .business-card {
    position: relative;
    width: 1000px; height: 572px;
    background: var(--card);
    overflow: hidden;
  }
  .brand-band {
    position: absolute; left: 0; top: 165px;
    width: 380px; height: 205px;
  }
  .brand-band svg { position: absolute; inset: 0; }
  .brand-band__name {
    position: absolute; left: 40px; top: 45px;
    font-weight: 500; font-size: 36px; line-height: 38px;
    color: var(--cream);
  }
  .holder {
    position: absolute; left: 455px; top: 95px;
    font-size: 30px; line-height: 34px; font-weight: 400;
  }
  .wordmark {
    position: absolute; left: 430px; top: 232px;
    display: flex; align-items: center; gap: 22px;
  }
  .wordmark__square {
    width: 70px; height: 70px; background: var(--accent);
  }
  .wordmark__name {
    font-weight: 500; font-size: 40px; line-height: 38px;
    color: var(--ink);
  }
  .contact {
    position: absolute; left: 410px; top: 395px;
    list-style: none;
    font-size: 27px; line-height: 34px;
  }
  .contact__item { display: flex; align-items: flex-start; gap: 14px; }
  .contact__icon { flex: 0 0 28px; width: 28px; height: 28px; margin-top: 3px; }
</style>
</head>
<body>
<main class="canvas">
  <section class="business-card">
    <div class="brand-band">
      <svg width="380" height="205" viewBox="0 0 380 205" aria-hidden="true">
        <polygon points="0,0 315,0 380,102 315,205 0,205" fill="var(--ink)"/>
      </svg>
      <p class="brand-band__name">Bright<br>Horizon<br>Guild</p>
    </div>

    <p class="holder">Neil P. Barton<br>CEO</p>

    <div class="wordmark">
      <span class="wordmark__square"></span>
      <p class="wordmark__name">Bright<br>Horizon<br>Guild</p>
    </div>

    <ul class="contact">
      <li class="contact__item">
        <svg class="contact__icon" viewBox="0 0 28 28" aria-hidden="true">
          <circle cx="14" cy="14" r="14" fill="var(--accent)"/>
          <path d="M14 6a5.5 5.5 0 0 0-5.5 5.5C8.5 16 14 22 14 22s5.5-6 5.5-10.5A5.5 5.5 0 0 0 14 6z" fill="var(--cream)"/>
          <circle cx="14" cy="11.5" r="2.2" fill="var(--accent)"/>
        </svg>
        <span>912 North Calloway Lane<br>Alder Springs, NV 89377</span>
      </li>
      <li class="contact__item">
        <svg class="contact__icon" viewBox="0 0 28 28" aria-hidden="true">
          <circle cx="14" cy="14" r="14" fill="var(--accent)"/>
          <rect x="7" y="9" width="14" height="10" rx="1.5" fill="var(--cream)"/>
          <path d="M7.5 9.5 14 15l6.5-5.5" fill="none" stroke="var(--accent)" stroke-width="1.5"/>
        </svg>
        <span>neil@brighthorizonguild.com</span>
      </li>
      <li class="contact__item">
        <svg class="contact__icon" viewBox="0 0 28 28" aria-hidden="true">
          <circle cx="14" cy="14" r="14" fill="var(--accent)"/>
          <path d="M6.5 14.5c0-3 3.4-5 7.5-5s7.5 2 7.5 5l-2.8 1.2-1.4-2.6c-2.2-.6-4.4-.6-6.6 0l-1.4 2.6z" fill="var(--cream)"/>
        </svg>
        <span>702-555-0182</span>
      </li>
    </ul>
  </section>
</main>
</body>
</html>
```